Dental Medical History Form - Content provided

Design a medical history form for a dental practice. Content is provided so all that is needed is the formatting to make it look great and easy to read.

"Patient Information" to include all information contained in top portion of the "Patient Medical History Form" docx file.

"Medical History" should follow the formatting and content of the "Exact Medical History" file as this is what the entry fields look like in our practice software and so we would like it to match.

1st page - Patient info, allergies, medications, antibiotics, joint replacement, pregnancy.

2nd page - Do you have, or have you had, any of the following? . . . . . . .
Updates

Target Market(s)

All ages but must be clear enough for elderly to read. Use as much space as possible to keep font size bigger yet keep to two pages

Industry/Entity Type

Dental

Font styles to use
Sans Serif

Requirements
Must have
• All content provided
• Our logo at the top (file provided)
• Century Gothic Font
• Limit to two pages

```html
<!DOCTYPE html>
<html lang="en">
<head>
<meta charset="utf-8">
<title>Medical History Form – Page 2</title>
<link rel="stylesheet" href="https://fonts.googleapis.com/css2?family=PT+Sans+Narrow:wght@400;700&display=swap">
<style>
  :root {
    --backdrop: #e6e7e9;
    --paper: #ffffff;
    --ink: #1f3550;
    --rule: #1f3550;
    --tab: #d9dadc;
    --tab-edge: #b9bbbe;
  }
  * { box-sizing: border-box; margin: 0; padding: 0; }
  html, body {
    width: 1200px; height: 784px; overflow: hidden;
    background: var(--backdrop);
    font-family: "PT Sans Narrow", "Arial Narrow", sans-serif;
    color: var(--ink);
  }
  .sheet {
    position: absolute; left: 296px; top: 6px;
    width: 608px; height: 772px;
    background: var(--paper);
    box-shadow: 0 2px 8px rgba(0,0,0,.12);
    padding: 18px 34px 0 34px;
  }
  .section-tab {
    margin-left: auto;
    width: 330px; height: 26px;
    background: linear-gradient(#e4e5e7, var(--tab));
    border-bottom: 1px solid var(--tab-edge);
    border-radius: 4px 0 0 4px;
    display: flex; align-items: center; justify-content: flex-end;
    padding-right: 10px;
    margin-right: -34px;
  }
  .section-title { font-size: 15px; font-weight: 700; }
  .columns {
    display: grid; grid-template-columns: 1fr 1fr; column-gap: 34px;
    margin-top: 10px;
  }
  .row {
    display: flex; align-items: center; height: 16.4px;
    font-size: 12.5px; line-height: 1;
  }
  .row .label { flex: 1; white-space: nowrap; }
  .row.group .label { font-weight: 700; font-size: 13px; }
  .answer { display: flex; align-items: center; gap: 4px; font-size: 11.5px; }
  .answer .opt-no { margin-left: 8px; }
  .box {
    width: 11px; height: 11px; border: 1px solid var(--ink); display: inline-block;
  }
  .sign-off {
    display: grid; grid-template-columns: 1fr 1fr; column-gap: 34px;
    margin-top: 22px;
  }
  .sign-field { display: flex; align-items: flex-end; gap: 8px; font-weight: 700; font-size: 14px; }
  .sign-line { flex: 1; border-bottom: 1px solid var(--rule); height: 14px; }
  .footer {
    position: absolute; left: 0; right: 0; bottom: 14px;
    display: flex; align-items: center; gap: 14px;
  }
  .footer-tab {
    width: 34px; height: 42px; background: linear-gradient(90deg, var(--tab-edge), var(--tab));
    border-radius: 0 4px 4px 0;
  }
  .footer-note { font-size: 10.5px; line-height: 1.4; padding-right: 34px; }
</style>
</head>
<body>
<main class="sheet">
  <header class="section-tab"><h1 class="section-title">Do you have, or have you had, any of the following?</h1></header>

  <section class="columns">
    <div class="column">
      <div class="row group"><span class="label">Dental</span></div>
      <div class="row"><span class="label">Acid Reflux</span><span class="answer">Yes <span class="box"></span><span class="opt-no">No</span> <span class="box"></span></span></div>
      <div class="row"><span class="label">Bad Breath/Taste</span><span class="answer">Yes <span class="box"></span><span class="opt-no">No</span> <span class="box"></span></span></div>
      <div class="row"><span class="label">Bleeding/Swollen/Sore Gums</span><span class="answer">Yes <span class="box"></span><span class="opt-no">No</span> <span class="box"></span></span></div>
      <div class="row"><span class="label">Blisters/Ulcers in Mouth</span><span class="answer">Yes <span class="box"></span><span class="opt-no">No</span> <span class="box"></span></span></div>
      <div class="row"><span class="label">Broken tooth/filling</span><span class="answer">Yes <span class="box"></span><span class="opt-no">No</span> <span class="box"></span></span></div>
      <div class="row"><span class="label">Burning tongue</span><span class="answer">Yes <span class="box"></span><span class="opt-no">No</span> <span class="box"></span></span></div>
      <div class="row"><span class="label">Dry mouth</span><span class="answer">Yes <span class="box"></span><span class="opt-no">No</span> <span class="box"></span></span></div>
      <div class="row"><span class="label">Food collection between teeth</span><span class="answer">Yes <span class="box"></span><span class="opt-no">No</span> <span class="box"></span></span></div>
      <div class="row"><span class="label">Grinding/clenching teeth (day/night)</span><span class="answer">Yes <span class="box"></span><span class="opt-no">No</span> <span class="box"></span></span></div>
      <div class="row"><span class="label">Loose teeth</span><span class="answer">Yes <span class="box"></span><span class="opt-no">No</span> <span class="box"></span></span></div>
      <div class="row"><span class="label">Crooked teeth</span><span class="answer">Yes <span class="box"></span><span class="opt-no">No</span> <span class="box"></span></span></div>
      <div class="row"><span class="label">Discoloured teeth</span><span class="answer">Yes <span class="box"></span><span class="opt-no">No</span> <span class="box"></span></span></div>
      <div class="row"><span class="label">Sensitivity to Hot/Cold</span><span class="answer">Yes <span class="box"></span><span class="opt-no">No</span> <span class="box"></span></span></div>
      <div class="row"><span class="label">Tooth pain when chewing</span><span class="answer">Yes <span class="box"></span><span class="opt-no">No</span> <span class="box"></span></span></div>
      <div class="row"><span class="label">Jaw pain/Fracture</span><span class="answer">Yes <span class="box"></span><span class="opt-no">No</span> <span class="box"></span></span></div>
      <div class="row"><span class="label">Orthodontic treatment/history</span><span class="answer">Yes <span class="box"></span><span class="opt-no">No</span> <span class="box"></span></span></div>
      <div class="row"><span class="label">Oral Cancer</span><span class="answer">Yes <span class="box"></span><span class="opt-no">No</span> <span class="box"></span></span></div>
      <div class="row group"><span class="label">Diet/Lifestyle</span></div>
      <div class="row"><span class="label">Drink more than one glass alcohol per day</span><span class="answer">Yes <span class="box"></span><span class="opt-no">No</span> <span class="box"></span></span></div>
      <div class="row"><span class="label">Smoking</span><span class="answer">Yes <span class="box"></span><span class="opt-no">No</span> <span class="box"></span></span></div>
      <div class="row"><span class="label">Carbonated drinks</span><span class="answer">Yes <span class="box"></span><span class="opt-no">No</span> <span class="box"></span></span></div>
      <div class="row"><span class="label">Sugary foods</span><span class="answer">Yes <span class="box"></span><span class="opt-no">No</span> <span class="box"></span></span></div>
      <div class="row group"><span class="label">Blood</span></div>
      <div class="row"><span class="label">Anaemia</span><span class="answer">Yes <span class="box"></span><span class="opt-no">No</span> <span class="box"></span></span></div>
      <div class="row"><span class="label">Blood clots</span><span class="answer">Yes <span class="box"></span><span class="opt-no">No</span> <span class="box"></span></span></div>
      <div class="row"><span class="label">Leukemia</span><span class="answer">Yes <span class="box"></span><span class="opt-no">No</span> <span class="box"></span></span></div>
      <div class="row"><span class="label">Low platelets</span><span class="answer">Yes <span class="box"></span><span class="opt-no">No</span> <span class="box"></span></span></div>
      <div class="row"><span class="label">Lymphoma</span><span class="answer">Yes <span class="box"></span><span class="opt-no">No</span> <span class="box"></span></span></div>
      <div class="row"><span class="label">Haemophilia</span><span class="answer">Yes <span class="box"></span><span class="opt-no">No</span> <span class="box"></span></span></div>
      <div class="row group"><span class="label">Chest</span></div>
      <div class="row"><span class="label">Bronchitis</span><span class="answer">Yes <span class="box"></span><span class="opt-no">No</span> <span class="box"></span></span></div>
      <div class="row"><span class="label">Cystic Fibrosis</span><span class="answer">Yes <span class="box"></span><span class="opt-no">No</span> <span class="box"></span></span></div>
      <div class="row"><span class="label">Emphysema</span><span class="answer">Yes <span class="box"></span><span class="opt-no">No</span> <span class="box"></span></span></div>
      <div class="row"><span class="label">Pneumonia</span><span class="answer">Yes <span class="box"></span><span class="opt-no">No</span> <span class="box"></span></span></div>
      <div class="row group"><span class="label">Infectious Disease</span></div>
      <div class="row"><span class="label">Creutzfeldt-Jakob Disease</span><span class="answer">Yes <span class="box"></span><span class="opt-no">No</span> <span class="box"></span></span></div>
      <div class="row"><span class="label">Hepatitis A,B,C,D</span><span class="answer">Yes <span class="box"></span><span class="opt-no">No</span> <span class="box"></span></span></div>
    </div>

    <div class="column">
      <div class="row"><span class="label">HIV/AIDS</span><span class="answer">Yes <span class="box"></span><span class="opt-no">No</span> <span class="box"></span></span></div>
      <div class="row"><span class="label">Influenza</span><span class="answer">Yes <span class="box"></span><span class="opt-no">No</span> <span class="box"></span></span></div>
      <div class="row"><span class="label">Shingles</span><span class="answer">Yes <span class="box"></span><span class="opt-no">No</span> <span class="box"></span></span></div>
      <div class="row"><span class="label">Tuberculosis</span><span class="answer">Yes <span class="box"></span><span class="opt-no">No</span> <span class="box"></span></span></div>
      <div class="row group"><span class="label">Heart</span></div>
      <div class="row"><span class="label">Angina</span><span class="answer">Yes <span class="box"></span><span class="opt-no">No</span> <span class="box"></span></span></div>
      <div class="row"><span class="label">Atrial Fibrillation</span><span class="answer">Yes <span class="box"></span><span class="opt-no">No</span> <span class="box"></span></span></div>
      <div class="row"><span class="label">Blood Pressure (High/Low)</span><span class="answer">Yes <span class="box"></span><span class="opt-no">No</span> <span class="box"></span></span></div>
      <div class="row"><span class="label">Congenital Heart Disease</span><span class="answer">Yes <span class="box"></span><span class="opt-no">No</span> <span class="box"></span></span></div>
      <div class="row"><span class="label">Heart attack</span><span class="answer">Yes <span class="box"></span><span class="opt-no">No</span> <span class="box"></span></span></div>
      <div class="row"><span class="label">Heart murmur</span><span class="answer">Yes <span class="box"></span><span class="opt-no">No</span> <span class="box"></span></span></div>
      <div class="row"><span class="label">Heart surgery</span><span class="answer">Yes <span class="box"></span><span class="opt-no">No</span> <span class="box"></span></span></div>
      <div class="row"><span class="label">Heart valve replacement</span><span class="answer">Yes <span class="box"></span><span class="opt-no">No</span> <span class="box"></span></span></div>
      <div class="row"><span class="label">Infective endocarditis</span><span class="answer">Yes <span class="box"></span><span class="opt-no">No</span> <span class="box"></span></span></div>
      <div class="row"><span class="label">Rheumatic Heart Disease</span><span class="answer">Yes <span class="box"></span><span class="opt-no">No</span> <span class="box"></span></span></div>
      <div class="row"><span class="label">Pacemaker</span><span class="answer">Yes <span class="box"></span><span class="opt-no">No</span> <span class="box"></span></span></div>
      <div class="row"><span class="label">Stent</span><span class="answer">Yes <span class="box"></span><span class="opt-no">No</span> <span class="box"></span></span></div>
      <div class="row group"><span class="label">Other</span></div>
      <div class="row"><span class="label">Anxiety/PTSD</span><span class="answer">Yes <span class="box"></span><span class="opt-no">No</span> <span class="box"></span></span></div>
      <div class="row"><span class="label">Arthritis</span><span class="answer">Yes <span class="box"></span><span class="opt-no">No</span> <span class="box"></span></span></div>
      <div class="row"><span class="label">Alzheimer's</span><span class="answer">Yes <span class="box"></span><span class="opt-no">No</span> <span class="box"></span></span></div>
      <div class="row"><span class="label">Asthma</span><span class="answer">Yes <span class="box"></span><span class="opt-no">No</span> <span class="box"></span></span></div>
      <div class="row"><span class="label">Anaphylaxis</span><span class="answer">Yes <span class="box"></span><span class="opt-no">No</span> <span class="box"></span></span></div>
      <div class="row"><span class="label">Auto-immune disease</span><span class="answer">Yes <span class="box"></span><span class="opt-no">No</span> <span class="box"></span></span></div>
      <div class="row"><span class="label">Coeliac</span><span class="answer">Yes <span class="box"></span><span class="opt-no">No</span> <span class="box"></span></span></div>
      <div class="row"><span class="label">Depression</span><span class="answer">Yes <span class="box"></span><span class="opt-no">No</span> <span class="box"></span></span></div>
      <div class="row"><span class="label">Diabetes</span><span class="answer">Yes <span class="box"></span><span class="opt-no">No</span> <span class="box"></span></span></div>
      <div class="row"><span class="label">Epilepsy</span><span class="answer">Yes <span class="box"></span><span class="opt-no">No</span> <span class="box"></span></span></div>
      <div class="row"><span class="label">Kidney Disease</span><span class="answer">Yes <span class="box"></span><span class="opt-no">No</span> <span class="box"></span></span></div>
      <div class="row"><span class="label">Liver Disease</span><span class="answer">Yes <span class="box"></span><span class="opt-no">No</span> <span class="box"></span></span></div>
      <div class="row"><span class="label">Osteoporosis</span><span class="answer">Yes <span class="box"></span><span class="opt-no">No</span> <span class="box"></span></span></div>
      <div class="row"><span class="label">Parkinson's</span><span class="answer">Yes <span class="box"></span><span class="opt-no">No</span> <span class="box"></span></span></div>
      <div class="row"><span class="label">Radiation to Head/Neck</span><span class="answer">Yes <span class="box"></span><span class="opt-no">No</span> <span class="box"></span></span></div>
      <div class="row"><span class="label">Schizophrenia</span><span class="answer">Yes <span class="box"></span><span class="opt-no">No</span> <span class="box"></span></span></div>
      <div class="row"><span class="label">Snoring</span><span class="answer">Yes <span class="box"></span><span class="opt-no">No</span> <span class="box"></span></span></div>
      <div class="row"><span class="label">Sleep apnea</span><span class="answer">Yes <span class="box"></span><span class="opt-no">No</span> <span class="box"></span></span></div>
      <div class="row"><span class="label">Stroke</span><span class="answer">Yes <span class="box"></span><span class="opt-no">No</span> <span class="box"></span></span></div>
    </div>
  </section>

  <section class="sign-off">
    <div class="sign-field">Date <span class="sign-line"></span></div>
    <div class="sign-field">Signature <span class="sign-line"></span></div>
  </section>

  <footer class="footer">
    <span class="footer-tab"></span>
    <p class="footer-note">Thank you for the time to complete your medical history form.<br>Oral health is linked to overall health and this comprehensive questionnaire will help us to provide you with optimal and safe care.</p>
  </footer>
</main>
</body>
</html>
```